Business Card Design for a Software Startup

We'd like to have a business card design. We already have a logo. Basically what we need is a clean design with name, address, cellphone and phone numbers, e-mail and web site address (front) and a space on the back with our logo with the company name on the right side and some texts on the bottom.
We are a development and consulting company in Brazil with highly qualified team of professionals in Java, iOS and Android development and consulting.

Target Market(s)

CIO, IT managers of mid to big size companies

Industry/Entity Type

Business

```html
<!DOCTYPE html>
<html lang="en">
<head>
<meta charset="utf-8">
<title>Vextra Business Card</title>
<link href="https://fonts.googleapis.com/css2?family=Arimo:wght@400;700&display=swap" rel="stylesheet">
<style>
  :root {
    --page: #e4e5ea;
    --card: #ffffff;
    --navy: #0d3f73;
    --deep: #123a6b;
    --bright: #1a9fdc;
    --ink: #3a3a3a;
    --rule: #c8c8c8;
  }
  * { margin: 0; padding: 0; box-sizing: border-box; }
  html, body {
    width: 1200px; height: 987px; overflow: hidden;
    background: var(--page);
    font-family: "Arimo", Arial, sans-serif;
  }
  .card {
    position: absolute;
    left: 230px;
    width: 740px; height: 430px;
    background: var(--card);
    border-radius: 34px;
    overflow: hidden;
    box-shadow: 0 6px 18px rgba(0,0,0,0.12);
  }
  .card-front { top: 45px; }
  .card-back { top: 512px; }

  .swoosh { position: absolute; left: 0; top: 0; width: 740px; height: 430px; }

  .brand {
    position: absolute; left: 52px; top: 42px;
    display: flex; align-items: center; gap: 22px;
  }
  .brand-square {
    width: 96px; height: 96px; border-radius: 14px;
    background: var(--navy);
  }
  .brand-name {
    font-weight: 700; font-size: 118px; line-height: 1;
    letter-spacing: 2px; color: var(--deep);
  }

  .identity {
    position: absolute; left: 40px; top: 218px; width: 262px;
    text-align: right; color: var(--ink);
  }
  .identity .person {
    font-weight: 700; font-size: 26px; color: var(--navy); margin-bottom: 4px;
  }
  .identity .title { font-size: 17px; margin-bottom: 10px; }
  .identity .address { font-size: 17px; line-height: 1.3; }

  .divider {
    position: absolute; left: 322px; top: 222px;
    width: 1px; height: 118px; background: var(--rule);
  }

  .contacts {
    position: absolute; left: 342px; top: 226px;
    list-style: none; font-size: 20px; line-height: 1.45; color: var(--ink);
  }
  .contacts .label { color: var(--navy); margin-right: 6px; }

  .back-brand {
    position: absolute; left: 0; right: 0; top: 118px;
    display: flex; justify-content: center; align-items: center; gap: 26px;
  }
  .back-brand .brand-square { width: 150px; height: 150px; border-radius: 22px; }
  .back-brand .brand-name { font-size: 92px; }
  .web {
    position: absolute; left: 0; right: 0; top: 330px;
    text-align: center; font-weight: 700; font-size: 22px;
    letter-spacing: 9px; color: var(--ink);
  }
</style>
</head>
<body>

<section class="card card-front">
  <svg class="swoosh" viewBox="0 0 740 430" aria-hidden="true">
    <path d="M0 250 C 70 290, 120 360, 230 400 C 330 436, 420 420, 520 430 L 0 430 Z" fill="var(--deep)"/>
    <path d="M0 262 C 80 310, 140 375, 250 408 C 340 432, 430 428, 520 430" fill="none" stroke="#ffffff" stroke-width="6"/>
    <path d="M0 270 C 90 322, 150 384, 262 414 C 350 436, 440 430, 530 432" fill="none" stroke="var(--bright)" stroke-width="3"/>
  </svg>

  <div class="brand">
    <div class="brand-square"></div>
    <div class="brand-name">VEXTRA</div>
  </div>

  <div class="identity">
    <div class="person">Your Name</div>
    <div class="title">Title</div>
    <div class="address">Door No. Street Name<br>City Name, State, Zip Code</div>
  </div>

  <div class="divider"></div>

  <ul class="contacts">
    <li><span class="label">p:</span>123-456-7890</li>
    <li><span class="label">c:</span>123-456-7890</li>
    <li><span class="label">e:</span>yourname@vextra.com</li>
    <li><span class="label">w:</span>www.vextra.com</li>
  </ul>
</section>

<section class="card card-back">
  <div class="back-brand">
    <div class="brand-square"></div>
    <div class="brand-name">VEXTRA</div>
  </div>
  <div class="web">www.vextra.com</div>
</section>

</body>
</html>
```